Sleek Design For Personal Brand Wordpress Website !!

*WORDPRESS WEBSITE*

Need a sleek and easy to navigate Wordpress website.

It will act as the hub for my personal brand.

Which means it will showcase all my social media outlets, host my most recent content like youtube videos and podcasts...

It will also be the go to place to find all my digital products and services that I offer.

i want it to be super sleek and simple but also give a personal touch of my who I really am. You can get a good idea of who I am my checking out my Instagram (@karim.dulvane)

Use these websites for ideas: www.bronvikel.com and www.teodorplaskewicz.com

Target Market(s)

Young Entrepreneurs

Industry/Entity Type

Education

Logo Text

Karim Dulvane

Number of Pages Required

4 page

Font styles to use
Sans Serif

Colors
ffffff
0392cd
ec1f27

Requirements
Must have
• Social Media buttons on the home page...
• Video (also a slider) right at the top of the home page...
• Email Optin...
• Multiple pages...

```html
<!DOCTYPE html>
<html lang="en">
<head>
<meta charset="utf-8">
<title>Ventrail Hub</title>
<link rel="stylesheet" href="https://fonts.googleapis.com/css2?family=Roboto:wght@400;500;700;900&display=swap">
<style>
:root{
  --red:#e31b23;
  --blue:#0d78c2;
  --ink:#222;
  --muted:#666;
  --grey:#e6e6e6;
  --white:#fff;
  --fb:#3b5998;--li:#0e76c5;--tw:#1da1f2;--ig:#a43bd1;
}
*{box-sizing:border-box;margin:0;padding:0}
html,body{width:1200px;height:2956px;overflow:hidden;background:var(--white);font-family:'Roboto',Arial,sans-serif;color:var(--ink)}
.page{position:relative;width:1200px;height:2956px}
.abs{position:absolute}
.logo{left:98px;top:20px;font-size:34px;font-weight:700;color:var(--red);letter-spacing:.5px}
.social{display:flex;gap:20px}
.social span{width:36px;height:36px;border-radius:50%;display:block}
.s-fb{background:var(--fb)}.s-li{background:var(--li)}.s-tw{background:var(--tw)}.s-ig{background:var(--ig)}
.header-social{left:890px;top:21px}
.nav{left:0;top:78px;width:1200px;height:48px;background:var(--red)}
.nav a{position:absolute;top:0;color:var(--white);text-decoration:none;font-size:13px;font-weight:700;line-height:48px;text-align:center;border-right:1px solid rgba(255,255,255,.45)}
.nav a:last-child{border-right:0}
.hero{left:0;top:126px;width:1200px;height:531px;background:radial-gradient(circle at 160px 110px,#f4c85a 0,#b3702e 8%,transparent 20%),radial-gradient(circle at 380px 350px,#8a4a2a 0,transparent 30%),linear-gradient(90deg,#3a2419,#5a3420 40%,#2a1b15)}
.hero-title{left:98px;top:262px;font-size:70px;font-weight:700;line-height:70px;color:var(--white)}
.hero-sub{left:98px;top:413px;font-size:24px;font-weight:500;color:var(--white)}
.slider{left:588px;top:194px;width:512px;height:396px;background:linear-gradient(135deg,#b9a08c,#7a5a48 50%,#3d2b22);border:2px solid #ddd}
.slider .arrow{position:absolute;top:178px;width:34px;height:40px;background:rgba(0,0,0,.55)}
.play{position:absolute;left:226px;top:168px;width:60px;height:60px;border-radius:50%;background:var(--white)}
.tile{width:322px;height:344px}
.t1{background:linear-gradient(#5b6470,#2c2f35)}.t2{background:linear-gradient(#6a5e55,#2a2420)}.t3{background:linear-gradient(#d8d4cc,#8e8a84)}
.t4{background:linear-gradient(#b3a79a,#5c5048)}.t5{background:linear-gradient(#c2a98a,#6e5a48)}.t6{background:linear-gradient(#8a949c,#3e454c)}
.training{left:0;top:1493px;width:1200px;height:565px;background:var(--grey)}
h2.sec-title{position:absolute;left:0;top:1543px;width:1200px;text-align:center;font-size:29px;font-weight:500}
.card-img{width:305px;height:241px}
.c1{background:linear-gradient(#9aa0a8,#3a3d42)}.c2{background:linear-gradient(#7a7a76,#38342e)}.c3{background:linear-gradient(#7c7f82,#2b2d30)}
.card-title{font-size:12px;font-weight:700;line-height:22px;width:300px;text-transform:uppercase}
.card-text{font-size:12px;color:var(--muted);line-height:23px;width:300px}
.services-h{left:100px;top:2126px;font-size:31px;font-weight:700;color:#333}
.services-t{left:273px;top:2108px;width:285px;font-size:12px;color:var(--muted);line-height:22px}
.svc-icon{width:80px;height:80px;border-radius:50%;background:var(--red)}
.svc-label{font-size:13px;font-weight:500;color:#333}
.news{left:0;top:2234px;width:1200px;height:298px;background:var(--blue)}
.news h3{position:absolute;left:98px;top:50px;font-size:29px;font-weight:700;color:var(--white)}
.news p{position:absolute;left:98px;top:104px;font-size:21px;color:var(--white)}
.field{position:absolute;top:168px;height:43px;background:var(--white);font-size:12px;color:#666;padding-left:12px;line-height:43px}
.btn{position:absolute;left:937px;top:168px;width:164px;height:43px;background:var(--red);color:var(--white);font-weight:700;font-size:16px;text-align:center;line-height:43px}
.foot-h{top:2584px;font-size:21px;font-weight:500;color:#333}
.foot-t{font-size:12px;color:var(--muted);line-height:25px}
.links{list-style:none}
.links li{font-size:12px;color:#444;line-height:26px;padding-left:28px;position:relative}
.links li::before{content:"»";position:absolute;left:0;color:var(--red);font-weight:700}
.contact li{font-size:12px;color:#444;line-height:25px;padding-left:30px;position:relative;list-style:none}
.contact svg{position:absolute;left:0;top:7px}
.rule{left:98px;top:2886px;width:1004px;height:1px;background:#ddd}
.copy{left:0;top:2914px;width:1200px;text-align:center;font-size:12px;color:#555}
</style>
</head>
<body>
<div class="page">
  <div class="abs logo">Ventrail Hub</div>
  <div class="abs social header-social" aria-label="Social media links"><span class="s-fb"></span><span class="s-li"></span><span class="s-tw"></span><span class="s-ig"></span></div>
  <nav class="abs nav">
    <a style="left:100px;width:132px">HOME</a>
    <a style="left:232px;width:166px">BLOG</a>
    <a style="left:398px;width:163px">PODCAST</a>
    <a style="left:561px;width:162px">EVENTS</a>
    <a style="left:723px;width:148px">BOOKS</a>
    <a style="left:871px;width:221px">HIRE ME TO SPEAK</a>
  </nav>

  <section class="abs hero" role="img" aria-label="Blurred warm restaurant lights background"></section>
  <div class="abs hero-title">VENTRAIL<br>HUB</div>
  <div class="abs hero-sub">Sed ut perspiciatis unde omnis iste natus</div>
  <div class="abs slider" role="img" aria-label="Featured video: host in a patterned shirt on a plaza">
    <div class="arrow" style="left:0"><svg width="34" height="40"><path d="M20 13l-7 7 7 7" stroke="#fff" stroke-width="2.5" fill="none"/></svg></div>
    <div class="arrow" style="right:0"><svg width="34" height="40"><path d="M14 13l7 7-7 7" stroke="#fff" stroke-width="2.5" fill="none"/></svg></div>
    <div class="play"><svg width="60" height="60"><path d="M24 17v26l20-13z" fill="#999"/></svg></div>
  </div>

  <div class="abs tile t1" style="left:98px;top:724px" role="img" aria-label="Podcast episode: host beside a helicopter"></div>
  <div class="abs tile t2" style="left:440px;top:724px" role="img" aria-label="Podcast episode: host in a robe taking a selfie"></div>
  <div class="abs tile t3" style="left:780px;top:724px" role="img" aria-label="Video: two young men looking at a phone"></div>
  <div class="abs tile t4" style="left:98px;top:1088px" role="img" aria-label="Video: man in a living room"></div>
  <div class="abs tile t5" style="left:440px;top:1088px" role="img" aria-label="Video: man in a cap holding a small dog"></div>
  <div class="abs tile t6" style="left:780px;top:1088px" role="img" aria-label="Podcast episode: host seated in a helicopter"></div>

  <section class="abs training"></section>
  <h2 class="sec-title">What You Will Learn On This FREE Training</h2>
  <div class="abs card-img c1" style="left:98px;top:1625px" role="img" aria-label="Sneakers, bag and watch on a bed"></div>
  <div class="abs card-img c2" style="left:448px;top:1625px" role="img" aria-label="Gold and blue wristwatch"></div>
  <div class="abs card-img c3" style="left:797px;top:1625px" role="img" aria-label="Group of friends with sports cars"></div>
  <div class="abs" style="left:98px;top:1890px"><div class="card-title">How you create a Shoplane store<br>that converts</div><div class="card-text" style="margin-top:8px">Building an eCommerce store is simple but building a store that actually makes people want to buy is more important!</div></div>
  <div class="abs" style="left:448px;top:1890px"><div class="card-title">How you find hot &amp; trending products<br>to cash out on</div><div class="card-text" style="margin-top:8px">Most people try to sell things that they personally like and want to buy... The secret is to find hot trends and capitalize on them while they're still hot!</div></div>
  <div class="abs" style="left:797px;top:1890px"><div class="card-title">How you can drive laser<br>targeted traffic</div><div class="card-text" style="margin-top:8px">After you build your store, add the hot and trending products the next step is to drive congruent traffic to generate sales!</div></div>

  <div class="abs services-h">SERVICES</div>
  <div class="abs services-t">Lorem ipsum dolor sit amet, consectetur adipiscing elit, sed do eiusmod tempor incididunt ut labore et dolore magna aliqua</div>
  <div class="abs svc-icon" style="left:606px;top:2106px"><svg width="80" height="80"><path d="M24 36h32l-4 18H28z" fill="#fff"/><path d="M32 36l6-10M48 36l-6-10" stroke="#fff" stroke-width="3"/></svg></div>
  <div class="abs svc-label" style="left:705px;top:2137px">eCommerce Expert</div>
  <div class="abs svc-icon" style="left:846px;top:2106px"><svg width="80" height="80"><path d="M26 26h16l14 14-16 16-14-14z" fill="#fff"/><circle cx="33" cy="33" r="3" fill="#e31b23"/></svg></div>
  <div class="abs svc-label" style="left:945px;top:2137px">FREE eCommerce</div>

  <section class="abs news">
    <h3>SUBSCRIBE TO NEWSLETTER</h3>
    <p>Neque porro quisquam est, qui dolorem ipsum quia dolor sit amet, consectetur</p>
    <svg class="abs" style="left:98px;top:150px" width="118" height="80"><path d="M4 34L88 4l26 58-84 14z" fill="#2a8fd3"/><path d="M4 34l58 16 52 12" stroke="#0d78c2" stroke-width="2" fill="none"/></svg>
    <div class="field" style="left:235px;width:340px">Your Name</div>
    <div class="field" style="left:587px;width:339px">Email Id</div>
    <div class="btn">SUBSCRIBE</div>
  </section>

  <div class="abs foot-h" style="left:98px">BLOG POST</div>
  <div class="abs" style="left:98px;top:2640px;width:200px;height:120px;background:linear-gradient(#8c8e90,#3d3e40);border:4px solid #eee" role="img" aria-label="Men playing table football"></div>
  <div class="abs foot-t" style="left:98px;top:2780px;width:240px">Lorem ipsum dolor sit amet, consectetur adipiscing elit. Integer varius, libero ac sodales ultrices, purus tortor volutpat sem,</div>
  <div class="abs foot-h" style="left:394px">ABOUT US</div>
  <div class="abs foot-t" style="left:394px;top:2632px;width:270px">Mauris nulla leo, aliquam sit amet libero vel, porta hendrerit erat. Aenean at diam efficitur, faucibus justo in, semper velit. Nulla ac quam pulvinar, aliquet lectus quis, consequat lorem. Integer euismod enim at dictum dictum. Duis nisl felis, blandit in sapien vitae, varius congue justo.<br><span style="color:var(--red)">Read More...</span></div>
  <div class="abs foot-h" style="left:708px">QUICK LINKS</div>
  <ul class="abs links" style="left:708px;top:2628px"><li>Home</li><li>Blog Podcast</li><li>Events</li><li>Books</li><li>Hire Me to Speak</li></ul>
  <div class="abs foot-h" style="left:913px">CONTACT US</div>
  <ul class="abs contact" style="left:913px;top:2628px">
    <li><svg width="12" height="10"><rect width="12" height="9" fill="#e31b23"/><path d="M0 0l6 5 6-5" stroke="#fff" fill="none"/></svg>support@ventrailhub.com</li>
    <li><svg width="12" height="12"><path d="M6 12C2 7 1 5 1 4a5 4 0 0110 0c0 1-1 3-5 8z" fill="#e31b23"/><circle cx="6" cy="4" r="1.6" fill="#fff"/></svg>ventrail hub building,</li>
    <li><svg width="12" height="12"><path d="M2 1l3 0 1 3-2 1a7 7 0 004 4l1-2 3 1v3c-6 0-10-4-10-10z" fill="#e31b23"/></svg>1-555-014-2290</li>
  </ul>
  <div class="abs social" style="left:913px;top:2735px"><span class="s-fb"></span><span class="s-li"></span><span class="s-tw"></span><span class="s-ig"></span></div>
  <div class="abs rule"></div>
  <div class="abs copy">Copyright © Ventrail Hub 2017 . All rights reserved.</div>
</div>
</body>
</html>
```